Bramblewood Joinery Website

My client Bramblewood Joinery is looking for a redesign for a Word Press Website. Their current site is at www.bramblewoodjoinery.example They are a custom cabinet company, but also create bathroom, living room, bar and entertainment and bedroom cabinets too. They would like a design that emulates the master craftsman work they do yet a contemporary style.

Their current site was designed using Flash elements.

Target Market(s)

Home owners and builders of high end homes

Industry/Entity Type

Entertainment

Font styles to use
Serif
Decorative

Requirements
Must have
• Must show their work and logo using a contemporary style.
Nice to have
• Sliders that showcase their projects.

```html
<!DOCTYPE html>
<html lang="en">
<head>
<meta charset="utf-8">
<title>Bramblewood Joinery</title>
<link href="https://fonts.googleapis.com/css2?family=Crimson+Text:wght@400;600&family=Open+Sans:ital,wght@0,400;0,600;1,400;1,600&display=swap" rel="stylesheet">
<style>
:root{
  --green:#3cb43c;
  --green-dark:#2e9a2e;
  --mint:#eaf5ea;
  --mint-col:#f1faf3;
  --text:#555;
  --dark:#333;
  --muted:#8a8a8a;
  --line:#d9d9d9;
}
*{box-sizing:border-box;margin:0;padding:0}
html,body{width:886px;height:1200px;overflow:hidden;background:#fff}
body{position:relative;font-family:"Open Sans",Arial,sans-serif;color:var(--text)}
.abs{position:absolute}
.topbar{left:0;top:0;width:886px;height:2px;background:var(--green)}
.header{left:0;top:2px;width:886px;height:110px;background:linear-gradient(#fafaf8,#f2f0ea)}
.brand{left:80px;top:36px;display:flex;align-items:center;gap:8px}
.brand-dot{width:22px;height:22px;border-radius:50%;background:var(--green)}
.brand-name{font-family:"Crimson Text",Georgia,serif;font-size:22px;font-weight:600;color:var(--green)}
.util{right:82px;top:30px;display:flex;gap:19px;align-items:center;font-style:italic;font-size:10.5px;color:var(--muted)}
.util .call{font-weight:600;font-size:13px;color:var(--dark);display:flex;align-items:center;gap:4px}
.util .call b{color:var(--green);font-weight:600}
.nav{right:82px;top:59px;display:flex;font-style:italic;font-size:10.5px;color:var(--dark)}
.nav a{display:block;padding:5px 13px;height:22px;text-decoration:none;color:inherit}
.nav a.active{background:var(--green);color:#fff;font-weight:600}
.hero{left:0;top:108px;width:886px;height:370px;background:linear-gradient(100deg,#6b4a35 0%,#c99a63 35%,#e0b47a 55%,#a9683e 75%,#d7a56d 100%)}
.zigzag{left:0;top:106px;width:886px;height:8px}
.arrow{top:240px;width:32px;height:91px;background:rgba(40,40,40,.55)}
.caption{left:0;top:478px;width:886px;height:76px;background:rgba(250,248,244,.96);text-align:center;border-bottom:1px dashed #aaa}
.caption h1{font-family:"Crimson Text",Georgia,serif;font-weight:400;font-size:30px;color:var(--green);margin-top:10px;line-height:1}
.caption p{font-style:italic;font-size:11.5px;color:var(--muted);margin-top:8px}
.caption p span{font-style:normal;color:var(--dark);display:inline-flex;align-items:center;gap:6px}
.col{top:555px;height:253px;text-align:center}
.col.mid{background:var(--mint-col);border-left:1px solid #e3ece5;border-right:1px solid #e3ece5}
.col .pic{width:190px;height:120px;margin:37px auto 0;border-radius:6px}
.col h3{font-family:"Crimson Text",Georgia,serif;font-weight:400;font-size:15px;color:var(--green);margin-top:16px}
.col p{font-size:10.5px;line-height:15px;margin:4px auto 0;max-width:214px}
.about-ribbon{left:80px;top:810px}
.about h2{left:126px;top:822px;font-family:"Crimson Text",Georgia,serif;font-weight:400;font-size:21px;color:var(--dark)}
.about h2 em{font-style:normal;color:var(--green)}
.rule{left:126px;top:855px;width:679px;height:1px;background:var(--line)}
.about-text{left:126px;top:864px;width:450px;font-size:10px;line-height:14.6px;color:#777}
.about-text p+p{margin-top:10px}
.btn-read{left:126px;top:974px;width:142px;height:25px;border:1px solid #9cd29c;border-radius:13px;background:linear-gradient(#fff,#e6f4e6);font-size:11px;font-weight:600;color:var(--dark);text-align:center;line-height:23px}
.video{left:583px;top:868px;width:222px;height:130px;background:linear-gradient(120deg,#e7d6bd,#c9a274 60%,#e9dcc8)}
.play{left:663px;top:902px}
.foot-line{left:0;top:1034px;width:886px;height:2px;background:var(--green)}
.foot-tri{left:90px;top:1036px}
.foot-nav{left:80px;top:1046px;display:flex;gap:20px;font-size:11px;color:var(--dark)}
.footer{left:0;top:1078px;width:886px;height:122px;background:var(--mint)}
.social{left:146px;top:1126px;display:flex;gap:5px}
.social span{width:24px;height:24px;border-radius:3px}
.copy{left:80px;top:1159px;width:270px;font-size:9.5px;line-height:13px;color:var(--dark)}
.news h4{left:366px;top:1106px;font-weight:400;font-size:13px;color:var(--dark)}
.news p{left:367px;top:1127px;font-size:9.5px;color:var(--dark)}
.email{left:367px;top:1151px;width:204px;height:27px;background:#fff;border:1px solid #dcdcdc}
.email-label{left:367px;top:1151px;width:56px;height:27px;background:var(--green);color:#fff;font-size:11.5px;font-weight:600;line-height:27px;text-align:center}
.email-go{left:547px;top:1156px}
.service{left:615px;top:1095px;font-size:9.5px;line-height:15px;color:var(--dark)}
.contact-ico{left:616px;top:1151px;width:36px;height:27px;background:var(--green)}
.contact-btn{left:655px;top:1151px;width:150px;height:27px;background:var(--green);color:#fff;font-size:13px;font-weight:600;line-height:27px;text-align:center}
</style>
</head>
<body>
<div class="abs topbar"></div>
<header class="abs header"></header>
<div class="abs brand"><span class="brand-dot"></span><span class="brand-name">Bramblewood Joinery</span></div>
<div class="abs util">
  <span>Professional</span><span>Portfolio</span><span>Cabinet Hardware</span>
  <span class="call"><svg width="11" height="11" viewBox="0 0 24 24"><path fill="#555" d="M6.6 10.8a15 15 0 0 0 6.6 6.6l2.2-2.2c.3-.3.7-.4 1-.2 1.1.4 2.3.6 3.6.6.6 0 1 .4 1 1V20c0 .6-.4 1-1 1A17 17 0 0 1 3 4c0-.6.4-1 1-1h3.5c.6 0 1 .4 1 1 0 1.3.2 2.5.6 3.6.1.3 0 .7-.2 1z"/></svg>Call Today..! <b>1-800-555-0142</b></span>
</div>
<nav class="abs nav">
  <a class="active">Home</a><a>Who We Are</a><a>Getting Started</a><a>Contact Us</a><a>Customer Experience</a>
</nav>

<div class="abs hero" role="img" aria-label="Slider photo of a finished kitchen with warm wood cabinets, granite counters and a stainless range"></div>
<svg class="abs zigzag" viewBox="0 0 886 8" preserveAspectRatio="none"><defs><pattern id="teeth" width="6" height="8" patternUnits="userSpaceOnUse"><path d="M0 0H6V2L3 8 0 2Z" fill="#f2f0ea"/></pattern></defs><rect width="886" height="8" fill="url(#teeth)"/></svg>
<div class="abs arrow" style="left:0"><svg width="32" height="91"><path d="M18 25 L10 45 L18 66" stroke="#eee" stroke-width="1.5" fill="none"/></svg></div>
<div class="abs arrow" style="left:854px"><svg width="32" height="91"><path d="M14 25 L22 45 L14 66" stroke="#eee" stroke-width="1.5" fill="none"/></svg></div>

<section class="abs caption">
  <h1>QUALITY ALL WOOD CABINETS</h1>
  <p>Lorem ipsum dolor sit amet consectetur adipiscing elit, Sed do euismod tempor magna aliqua. <span>LEARN MORE <svg width="17" height="17" viewBox="0 0 20 20"><circle cx="10" cy="10" r="8.5" fill="none" stroke="#3cb43c" stroke-width="1.8"/><path d="M5.5 10h8M10.5 6.8 13.8 10l-3.3 3.2" stroke="#3cb43c" stroke-width="1.8" fill="none"/></svg></span></p>
</section>

<article class="abs col" style="left:0;width:318px">
  <div class="pic" role="img" aria-label="Render of a wooden fitted kitchen" style="background:linear-gradient(135deg,#e9d2b2,#c0824c 55%,#f1ece6)"></div>
  <h3>KITCHENS</h3>
  <p>Our cabinets come fully loaded! While other cabinet companies charge for...</p>
</article>
<article class="abs col mid" style="left:318px;width:251px">
  <div class="pic" role="img" aria-label="Sketch of a kitchen design layout" style="background:linear-gradient(135deg,#eef1f2,#aeb7bc 55%,#f4f6f6)"></div>
  <h3>DESIGN SERVICES</h3>
  <p>Our cabinets come fully loaded! While other cabinet companies charge for...</p>
</article>
<article class="abs col" style="left:569px;width:317px">
  <div class="pic" role="img" aria-label="Installers fitting kitchen cabinets" style="background:linear-gradient(135deg,#f2e6d4,#c99b6a 55%,#efe6da)"></div>
  <h3>KITCHENS</h3>
  <p>Our cabinets come fully loaded! While other cabinet companies charge for...</p>
</article>

<svg class="abs about-ribbon" width="38" height="54" viewBox="0 0 38 54"><path d="M0 0H38V54L19 44 0 54Z" fill="var(--green)"/><circle cx="19" cy="24" r="7" fill="#fff"/></svg>
<div class="about">
  <h2 class="abs">About <em>BRAMBLEWOOD</em> Joinery &amp; Fixtures</h2>
</div>
<div class="abs rule"></div>
<div class="abs about-text">
  <p>Lorem ipsum dolor sit amet, consectetur adipiscing elit, sed do eiusmod tempor incididunt ut labore et dolore magna aliqua. Ut enim ad minim veniam, quis nostrud exercitation ullamco laboris nisi ut aliquip ex ea commodo consequat.</p>
  <p>Ut enim ad minim orem ipsum dolor sit amet, consectetur adipiscing elit, sed do eiusmod tempor incididunt ut labore et dolore magna aliqua. Ut enim ad minim veniam, quis nostrud exercitation ullamco laboris nisi ut aliquip ex ea commodo consequat.</p>
</div>
<div class="abs btn-read">Continue Reading...</div>
<div class="abs video" role="img" aria-label="Video still of a bright wooden kitchen"></div>
<svg class="abs play" width="62" height="62" viewBox="0 0 62 62"><circle cx="31" cy="31" r="27" fill="none" stroke="#3cb43c" stroke-width="6" opacity=".85"/><path d="M25 19 44 31 25 43Z" fill="#3cb43c" opacity=".85"/></svg>

<div class="abs foot-line"></div>
<svg class="abs foot-tri" width="10" height="6"><path d="M0 0H10L5 6Z" fill="var(--green)"/></svg>
<nav class="abs foot-nav"><span>Home</span><span>Who We Are</span><span>Getting Started</span><span>Contact Us</span><span>Customer Experience</span><span>Professional</span><span>Portfolio</span><span>Cabinet Hardware</span></nav>

<footer class="abs footer"></footer>
<div class="abs social"><span style="background:#3b5a9a"></span><span style="background:#333"></span><span style="background:#c9202b"></span><span style="background:#2aa9e0"></span></div>
<div class="abs copy">Copyrights © 2015 bramblewoodjoinery.example<br>All Rights Reserved</div>
<div class="news"><h4 class="abs">Newsletter</h4><p class="abs">Join us to start receiving news about new</p></div>
<div class="abs email"></div>
<div class="abs email-label">Email</div>
<svg class="abs email-go" width="17" height="17" viewBox="0 0 20 20"><circle cx="10" cy="10" r="8.5" fill="none" stroke="#666" stroke-width="1.6"/><path d="M5.5 10h8M10.5 6.8 13.8 10l-3.3 3.2" stroke="#666" stroke-width="1.6" fill="none"/></svg>
<div class="abs service">Service Centers<br>88 Alder Lane, Suite 210<br>Millbrook 4521</div>
<div class="abs contact-ico"><svg width="36" height="27" viewBox="0 0 36 27"><path transform="translate(11 6) scale(.6)" fill="#fff" d="M6.6 10.8a15 15 0 0 0 6.6 6.6l2.2-2.2c.3-.3.7-.4 1-.2 1.1.4 2.3.6 3.6.6.6 0 1 .4 1 1V20c0 .6-.4 1-1 1A17 17 0 0 1 3 4c0-.6.4-1 1-1h3.5c.6 0 1 .4 1 1 0 1.3.2 2.5.6 3.6.1.3 0 .7-.2 1z"/></svg></div>
<div class="abs contact-btn">Contact Us Today..!</div>
</body>
</html>
```